Business Card Design for Varomir Facility Services

We are looking for a Business Card Design for the Company "Varomir Facility Services."
Front side:
- Company Logo (small)
- Company Name, address, pohone, website and personal data.
- white background, for text e.g. company colors (blue or green like in the logo)
Please use following data:
Company data:
Varomir Facility Services Kostelac
Birkenhaldweg 14
6330 Cham
www.varomir-fs.ch
Person data:
Tarik Kostelac
Geschäftsführer
+41 76 519 47 83
info@varomir-fs.ch
Back side:
could be colored in blue or green
please use a big logo sing and some smaller icons to say what is all beeing offered in facility services, like cleaning, maintenance cleaning
industrial cleaning, caretaking, gardening, disposal. There is no need for everyone of the icons if there are similar or an icon is standing for more of them.
colors to use:
blue: HEX 246BB0
green: HEX 52B33E

```html
<!DOCTYPE html>
<html lang="de">
<head>
<meta charset="utf-8">
<title>Varomir Facility Services – Visitenkarte</title>
<link rel="stylesheet" href="https://fonts.googleapis.com/css2?family=Poppins:wght@400;600;700&family=Roboto:wght@400;500&display=swap">
<style>
  :root {
    --brand-blue: #246BB0;
    --deep-blue: #1356A6;
    --brand-green: #52B33E;
    --contact-green: #1E9E3A;
    --ink: #1b1b1b;
    --paper: #ffffff;
    --backdrop: #e9eaec;
  }
  * { box-sizing: border-box; margin: 0; padding: 0; }
  html, body { width: 1200px; height: 1200px; overflow: hidden; }
  body {
    background: var(--backdrop);
    font-family: "Roboto", Arial, sans-serif;
    position: relative;
  }
  .card {
    position: absolute;
    left: 170px;
    width: 860px;
    height: 500px;
    border-radius: 34px;
    overflow: hidden;
    box-shadow: 0 10px 28px rgba(0,0,0,.18);
  }

  /* Back side */
  .card-back { top: 60px; background: var(--brand-blue); color: var(--paper); }
  .back-wordmark {
    position: absolute; top: 110px; left: 0; right: 0;
    display: flex; align-items: center; justify-content: center; gap: 22px;
  }
  .back-wordmark .mark-dot {
    width: 64px; height: 64px; border-radius: 50%; background: var(--paper);
  }
  .back-wordmark .name {
    font-family: "Poppins", Arial, sans-serif; font-weight: 600;
    font-size: 50px; letter-spacing: 1px; color: var(--paper);
  }
  .service-list {
    position: absolute; top: 300px; left: 0; right: 0;
    display: flex; justify-content: center; gap: 48px; list-style: none;
  }
  .service { width: 130px; text-align: center; }
  .service-icon {
    width: 96px; height: 96px; margin: 0 auto 12px;
    border-radius: 50%; border: 4px solid var(--paper);
    display: flex; align-items: center; justify-content: center;
  }
  .service-icon .icon-fill {
    width: 74px; height: 74px; border-radius: 50%; background: var(--paper);
  }
  .service-icon svg { display: block; }
  .service-label {
    font-family: "Poppins", Arial, sans-serif; font-weight: 600;
    font-size: 13px; line-height: 1.15; text-transform: uppercase; letter-spacing: .3px;
  }

  /* Front side */
  .card-front { top: 630px; background: var(--paper); }
  .front-wordmark {
    position: absolute; top: 52px; left: 58px;
    display: flex; align-items: center; gap: 16px;
  }
  .front-wordmark .mark-dot {
    width: 46px; height: 46px; border-radius: 50%; background: var(--brand-green);
  }
  .front-wordmark .name {
    font-family: "Poppins", Arial, sans-serif; font-weight: 600;
    font-size: 36px; color: var(--brand-blue);
  }
  .person { position: absolute; top: 196px; left: 0; }
  .person-marker {
    position: absolute; left: 0; top: 4px; width: 30px; height: 58px; background: var(--deep-blue);
  }
  .person-name {
    margin-left: 54px;
    font-family: "Poppins", Arial, sans-serif; font-weight: 700;
    font-size: 34px; color: var(--deep-blue); line-height: 1.1;
  }
  .person-role { margin-left: 54px; font-size: 19px; color: var(--ink); }
  .contact {
    position: absolute; right: 56px; top: 262px; width: 430px;
    font-size: 20px; color: var(--ink); line-height: 1.3;
  }
  .contact-company { font-weight: 500; color: var(--contact-green); font-size: 21px; }
  .contact-address { margin-bottom: 8px; }
  .contact-row { display: flex; align-items: center; gap: 10px; }
  .contact-row svg { flex: none; }
  .contact-row .web-core { color: var(--deep-blue); font-weight: 500; }
  .front-band {
    position: absolute; left: 0; right: 0; bottom: 0; height: 30px; background: var(--deep-blue);
  }
</style>
</head>
<body>

<section class="card card-back" aria-label="Rückseite">
  <div class="back-wordmark">
    <span class="mark-dot"></span>
    <span class="name">Varomir Facility Services</span>
  </div>
  <ul class="service-list">
    <li class="service">
      <div class="service-icon"><span class="icon-fill" role="img" aria-label="Symbol Unterhaltsreinigung: Besen"></span></div>
      <div class="service-label">Maintenance<br>Cleaning</div>
    </li>
    <li class="service">
      <div class="service-icon"><span class="icon-fill" role="img" aria-label="Symbol Hauswartung: Handschlag mit Herz"></span></div>
      <div class="service-label">Caretaking</div>
    </li>
    <li class="service">
      <div class="service-icon"><span class="icon-fill" role="img" aria-label="Symbol Gartenpflege: Blume im Topf"></span></div>
      <div class="service-label">Gardening</div>
    </li>
    <li class="service">
      <div class="service-icon">
        <svg width="52" height="58" viewBox="0 0 52 58" aria-label="Symbol Entsorgung: Mülleimer" role="img">
          <rect x="4" y="8" width="44" height="6" rx="2" fill="#fff"/>
          <rect x="19" y="2" width="14" height="6" rx="2" fill="#fff"/>
          <path d="M8 17h36l-4 39H12z" fill="#fff"/>
          <g stroke="#246BB0" stroke-width="3"><line x1="18" y1="23" x2="19" y2="50"/><line x1="26" y1="23" x2="26" y2="50"/><line x1="34" y1="23" x2="33" y2="50"/></g>
        </svg>
      </div>
      <div class="service-label">Disposal</div>
    </li>
  </ul>
</section>

<section class="card card-front" aria-label="Vorderseite">
  <div class="front-wordmark">
    <span class="mark-dot"></span>
    <span class="name">Varomir Facility Services</span>
  </div>

  <div class="person">
    <span class="person-marker"></span>
    <p class="person-name">Tarik Kostelac</p>
    <p class="person-role">Geschäftsführer</p>
  </div>

  <div class="contact">
    <p class="contact-company">Varomir Facility Services Kostelac</p>
    <p class="contact-address">Birkenhaldweg 14 6330 Cham</p>
    <p class="contact-row">
      <svg width="18" height="18" viewBox="0 0 24 24" aria-hidden="true"><path fill="#1356A6" d="M6.6 10.8a15 15 0 0 0 6.6 6.6l2.2-2.2a1 1 0 0 1 1-.25 11.4 11.4 0 0 0 3.6.57 1 1 0 0 1 1 1V20a1 1 0 0 1-1 1A17 17 0 0 1 3 4a1 1 0 0 1 1-1h3.5a1 1 0 0 1 1 1c0 1.25.2 2.45.57 3.57a1 1 0 0 1-.25 1z"/></svg>
      <span>+41 76 519 47 83</span>
    </p>
    <p class="contact-row">
      <svg width="18" height="18" viewBox="0 0 24 24" aria-hidden="true"><rect x="2" y="5" width="20" height="14" rx="2" fill="#1356A6"/><path d="M3 6l9 7 9-7" fill="none" stroke="#fff" stroke-width="1.8"/></svg>
      <span>info@varomir-fs.ch</span>
    </p>
    <p class="contact-row">
      <svg width="18" height="18" viewBox="0 0 24 24" aria-hidden="true"><g fill="none" stroke="#1356A6" stroke-width="1.8"><circle cx="12" cy="12" r="9.5"/><ellipse cx="12" cy="12" rx="4.2" ry="9.5"/><line x1="2.5" y1="12" x2="21.5" y2="12"/><line x1="4" y1="7" x2="20" y2="7"/><line x1="4" y1="17" x2="20" y2="17"/></g></svg>
      <span>www.<span class="web-core">varomir-fs</span>.ch</span>
    </p>
  </div>

  <div class="front-band"></div>
</section>

</body>
</html>
```